Nimbo31.com.au Website and company image design

We are looking for an exceptional website designer / company to work with our new Australian Hosting Company

Nimbo31 is a new Cloud Hosting company launching in Australia that provides Scalable, On Demand computing resources to the Australian Market Place. Scalable, On Demand ocmputing is a nice way of saying fully scalable / redundant Virtual Private Server.

We require a full company image to be developed along with a Logo and Website. There is scope for ongoing development (preferred) for the successful candidate.

Website developement will require extensive jQuery ability (sliders for ordering etc (see: http://www.hostrivo.com.au/virtual-dedicated-servers/253/kelp_vps.html).

Please communicate directly with me to establish full website scope and request further documentation / content.

Target Market(s)

Website Designers, programmers, technicians and large companies

Industry/Entity Type

It Company

Requirements
Must have
• Slider ordering system such as http://www.hostrivo.com.au/virtual-dedicated-servers/253/kelp_vps.html

Nice to have
• CMS backend system
Should not have
• Should NOT be a monster template copy!!!

```html
<!DOCTYPE html>
<html lang="en">
<head>
<meta charset="utf-8">
<title>Nimbo31 – Cloud Hosting &amp; VPS Hosting</title>
<link href="https://fonts.googleapis.com/css2?family=Oswald:wght@400;500&family=Open+Sans:wght@400;600;700&family=Nunito:wght@300;400&display=swap" rel="stylesheet">
<style>
:root{
  --blue:#4aa6ec;
  --blue-dark:#2f86cf;
  --sky:#e6f1fb;
  --ink:#2b2b2b;
  --text:#3d3d3d;
  --muted:#6d6d6d;
  --band:#f3f3f3;
  --rule:#e2e2e2;
  --btn-dark:#353a40;
  --white:#ffffff;
}
*{box-sizing:border-box;margin:0;padding:0}
html,body{width:781px;height:1200px;overflow:hidden;background:var(--white)}
body{position:relative;font-family:"Open Sans",Arial,sans-serif;color:var(--text);font-size:8px}
.abs{position:absolute}
ul{list-style:none}

/* header */
.header{left:0;top:0;width:781px;height:84px;background:linear-gradient(#dcebf8,#fff 70%);border-bottom:1px solid #8fc2ec}
.toplinks{right:95px;top:8px;display:flex;gap:14px;align-items:center;font-size:7.5px;color:var(--ink)}
.toplinks span{display:flex;align-items:center;gap:4px}
.login{background:linear-gradient(#f4f8fc,#dbe7f2);border:1px solid #c5d6e6;border-radius:9px;padding:2px 8px;color:var(--blue)}
.logo{left:100px;top:26px;display:flex;align-items:center;gap:6px;font-family:"Open Sans",sans-serif;font-weight:700;font-size:22px;color:var(--blue)}
.logo i{width:16px;height:16px;border-radius:50%;background:var(--blue);display:block}
.chat{left:522px;top:41px}
.chat h2{font-family:"Nunito",sans-serif;font-weight:300;font-size:18px;color:var(--blue);line-height:1}
.chat p{font-size:5.5px;color:var(--ink);margin-top:2px}
.chat-bubble{left:646px;top:38px}

/* nav */
.nav{left:0;top:84px;width:781px;height:46px;background:linear-gradient(#fff,#eef3f8);border-bottom:1px solid #e5e9ee}
.nav ul{position:absolute;left:90px;top:0;display:flex;height:46px}
.nav li{height:46px;display:flex;flex-direction:column;align-items:center;justify-content:flex-end;padding:0 13px 6px;color:var(--blue);font-size:10px;gap:6px}
.nav li.active{background:var(--blue);color:var(--white);padding:0 15px 6px}

/* hero */
.hero-art{left:125px;top:158px;width:175px;height:190px;background:radial-gradient(ellipse at 50% 45%,#2e2e2e,#1b1b1b 40%,#ffffff 72%)}
.hero-title{left:328px;top:222px;font-family:"Oswald",sans-serif;font-weight:500;font-size:27px;color:var(--blue);letter-spacing:.3px}
.hero-tag{left:353px;top:259px;font-size:10.5px;color:var(--ink)}
.dots{left:374px;top:327px;display:flex;gap:5px}
.dots i{width:7px;height:7px;border-radius:50%;background:#dcdcdc;display:block}
.dots i:first-child{background:var(--blue)}

/* intro band */
.band{left:0;top:352px;width:781px;height:76px;background:var(--band);text-align:center;font-family:"Nunito",sans-serif}
.band p{font-size:16px;line-height:21px;color:var(--ink)}
.band p:first-child{margin-top:14px}
.band em{font-style:normal;color:var(--blue)}

/* plans */
.plan{top:452px;width:200px;height:232px;text-align:center}
.plan h3{font-family:"Oswald",sans-serif;font-weight:500;font-size:13px;color:var(--ink)}
.plan .icon{margin:13px auto 0;width:52px;height:52px;border-radius:50%;background:radial-gradient(#fff 60%,#eceff2);box-shadow:0 1px 3px rgba(0,0,0,.08);display:flex;align-items:center;justify-content:center}
.plan .price{margin-top:8px;font-family:"Oswald",sans-serif;font-size:11px;color:var(--ink)}
.plan .price b{font-weight:400;font-size:21px;color:var(--blue)}
.plan .desc{font-size:6.8px;color:var(--blue);margin:3px 10px 0;line-height:9px;height:18px}
.plan ul{text-align:left;margin:10px 0 0 22px}
.plan li{font-size:7px;line-height:14.5px;color:var(--ink)}
.plan li::before,.list li::before{content:"»";color:var(--blue);margin-right:8px}
.btn{position:absolute;left:52px;top:200px;width:95px;height:20px;border-radius:5px;background:var(--btn-dark);color:#fff;font-family:"Oswald",sans-serif;font-size:12px;line-height:20px;text-align:center}
.btn.blue{background:var(--blue)}
.vrule{top:440px;width:1px;height:480px;background:linear-gradient(transparent,var(--rule) 15%,var(--rule) 85%,transparent)}
.hrule{left:95px;top:688px;width:590px;height:1px;background:var(--rule)}

/* lower columns */
.col-h{top:697px;font-family:"Oswald",sans-serif;font-weight:500;font-size:13px;color:var(--ink)}
.diff{left:108px;top:725px;width:157px;font-size:7px;line-height:14.5px;text-align:justify;color:var(--ink)}
.diff .link{color:var(--blue);margin-top:4px;text-align:left}
.twocol{left:108px;top:831px;display:flex;gap:30px}
.list li{font-size:7px;line-height:14.5px;color:var(--ink)}
.facilities{left:298px;top:737px;width:182px}
.facilities li{font-size:7.5px;line-height:18px;padding-left:20px;color:var(--ink)}
.facilities li:first-child{background:linear-gradient(90deg,#f0f0f0,#fff)}
.story{left:503px;display:flex;gap:9px;width:172px}
.story .thumb{width:76px;height:50px;flex:none;border:2px solid #fff;box-shadow:0 0 3px rgba(0,0,0,.25);display:flex;align-items:center;justify-content:center;font-weight:700;font-size:9px}
.story p{font-size:6.8px;line-height:11px;color:var(--ink)}
.story p span{display:block;text-align:right;color:var(--blue)}
.arrows{left:651px;top:717px;display:flex;gap:3px}
.arrows i{width:11px;height:11px;border-radius:50%;background:var(--blue);display:block}

/* footer */
.footer{left:0;top:940px;width:781px;height:185px;background:var(--band)}
.foot-h{top:958px;font-family:"Oswald",sans-serif;font-size:13px;color:#555}
.about{left:108px;top:985px;width:193px;font-size:7.5px;line-height:14.5px;color:var(--ink)}
.more{left:265px;top:1077px;font-family:"Oswald",sans-serif;font-size:9px;color:var(--blue)}
.field{left:337px;width:162px;height:22px;border:1px solid #dcdcdc;border-radius:5px;background:#fff;font-size:7px;color:#aaa;padding:4px 10px}
.submit{left:369px;top:1099px;width:95px;height:20px;border-radius:5px;background:var(--btn-dark);color:#fff;font-family:"Oswald",sans-serif;font-size:12px;line-height:20px;text-align:center}
.social{left:545px;top:990px}
.social li{display:flex;align-items:center;gap:9px;height:27.5px;font-weight:700;font-size:10.5px;color:var(--ink)}
.social li i{width:18px;height:18px;background:var(--ink);display:block}
.social li:first-child{color:var(--blue)}
.social li:first-child i{background:var(--blue)}
.bottom{left:0;top:1125px;width:781px;height:75px;background:linear-gradient(#ffffff,var(--sky))}
.copy{left:0;top:1170px;width:781px;text-align:center;font-size:6.5px;color:var(--ink)}
</style>
</head>
<body>

<header class="abs header">
  <div class="abs toplinks">
    <span><svg width="8" height="10" viewBox="0 0 8 10"><path d="M2 0 L4 3 L3 4 Q4 6 5 7 L6 6 L8 8 L6 10 Q0 7 0 2Z" fill="#4aa6ec"/></svg>888-9-Nimbo31</span>
    <span><svg width="12" height="9" viewBox="0 0 12 9"><rect x=".5" y=".5" width="11" height="8" fill="none" stroke="#4aa6ec"/><path d="M.5 .5 L6 5 L11.5 .5" fill="none" stroke="#4aa6ec"/></svg>Email Us</span>
    <span><svg width="9" height="11" viewBox="0 0 9 11"><rect x=".5" y=".5" width="8" height="10" fill="none" stroke="#4aa6ec"/><path d="M2 3h5M2 5h5M2 7h5" stroke="#4aa6ec"/></svg>Get a Quote</span>
    <span class="login">Client Login</span>
  </div>
  <div class="abs logo"><i></i>Nimbo31</div>
  <div class="abs chat"><h2>Chat With Us !</h2><p>Together we can quickly meet your needs</p></div>
  <svg class="abs chat-bubble" width="34" height="32" viewBox="0 0 34 32" aria-hidden="true">
    <ellipse cx="22" cy="11" rx="11" ry="9" fill="#dfe9f2"/>
    <ellipse cx="15" cy="19" rx="14" ry="11" fill="#3a9de8"/>
    <path d="M6 26 L3 32 L12 28Z" fill="#3a9de8"/>
  </svg>
</header>

<nav class="abs nav">
  <ul>
    <li class="active"><svg width="16" height="14" viewBox="0 0 16 14"><path d="M8 0 L16 7 H13 V14 H3 V7 H0Z" fill="#fff"/></svg>Home</li>
    <li><svg width="12" height="14" viewBox="0 0 12 14"><rect width="12" height="14" rx="1" fill="#4aa6ec"/><circle cx="6" cy="5" r="2" fill="#fff"/></svg>About Us</li>
    <li><svg width="16" height="14" viewBox="0 0 16 14"><rect width="16" height="4" fill="#4aa6ec"/><rect y="5" width="16" height="4" fill="#4aa6ec"/><rect y="10" width="16" height="4" fill="#4aa6ec"/></svg>Dedicated</li>
    <li><svg width="20" height="12" viewBox="0 0 20 12"><path d="M4 12 Q0 12 1 8 Q2 5 6 6 Q7 0 13 2 Q17 3 16 6 Q20 7 19 10 Q18 12 16 12Z" fill="#4aa6ec"/></svg>Cloud</li>
    <li><svg width="18" height="14" viewBox="0 0 18 14"><circle cx="6" cy="9" r="5" fill="#4aa6ec"/><circle cx="13" cy="4" r="4" fill="#4aa6ec"/></svg>Colocation</li>
    <li><svg width="24" height="14" viewBox="0 0 24 14"><rect x="9" width="6" height="5" fill="#4aa6ec"/><rect y="9" width="6" height="5" fill="#4aa6ec"/><rect x="9" y="9" width="6" height="5" fill="#4aa6ec"/><rect x="18" y="9" width="6" height="5" fill="#4aa6ec"/><path d="M12 5V9M3 9V7H21V9" stroke="#4aa6ec" fill="none"/></svg>Management</li>
    <li><svg width="14" height="14" viewBox="0 0 14 14"><path d="M7 0 L14 3.5 L7 7 L0 3.5Z" fill="#4aa6ec"/><path d="M0 7 L7 10.5 L14 7M0 10 L7 13.5 L14 10" stroke="#4aa6ec" fill="none" stroke-width="1.5"/></svg>Solutions</li>
    <li><svg width="13" height="13" viewBox="0 0 8 10"><path d="M2 0 L4 3 L3 4 Q4 6 5 7 L6 6 L8 8 L6 10 Q0 7 0 2Z" fill="#4aa6ec"/></svg>Contact Us</li>
  </ul>
</nav>

<div class="abs hero-art" role="img" aria-label="Three black tower servers standing together"></div>
<h1 class="abs hero-title">CLOUD HOSTING &amp; VPS HOSTING</h1>
<p class="abs hero-tag">Reliable &nbsp;|&nbsp; Affordable &nbsp;|&nbsp; Scalable &nbsp;|&nbsp; Managed &nbsp;|&nbsp; Unmanaged</p>
<div class="abs dots"><i></i><i></i><i></i></div>

<section class="abs band">
  <p><em>Nimbo31</em> is a leading Internet Technology provider.</p>
  <p>Our solutions add real business value to customers worldwide.</p>
</section>

<div class="abs vrule" style="left:285px"></div>
<div class="abs vrule" style="left:489px"></div>

<section class="abs plan" style="left:84px">
  <h3>DEDICATED SERVERS</h3>
  <div class="icon"><svg width="26" height="24" viewBox="0 0 26 24"><rect width="26" height="6" rx="2" fill="#5aa9e6"/><rect y="9" width="26" height="6" rx="2" fill="#8a99a8"/><rect y="18" width="26" height="6" rx="2" fill="#5aa9e6"/></svg></div>
  <p class="price">STARTING AT <b>$199</b>/MO</p>
  <p class="desc">High performance servers with the reliability and uptime you need</p>
  <ul><li>Dual Power Supplies</li><li>Dual Network Connections</li><li>RAID Data Protection &amp; Off-Site Backup</li></ul>
  <span class="btn blue">VIEW PLANS</span>
</section>

<section class="abs plan" style="left:279px">
  <h3>CLOUD SERVERS</h3>
  <div class="icon"><svg width="30" height="20" viewBox="0 0 20 12"><path d="M4 12 Q0 12 1 8 Q2 5 6 6 Q7 0 13 2 Q17 3 16 6 Q20 7 19 10 Q18 12 16 12Z" fill="#fff" stroke="#4aa6ec" stroke-width="1.3"/></svg></div>
  <p class="price">STARTING AT <b>$169</b>/MO</p>
  <p class="desc">Our Cloud Servers are powered by Hypervia 100% Uptime</p>
  <ul><li>Hypervia and Kelp Cloud</li><li>Enterprise Ready</li><li>Fully Redundant 100% Uptime</li></ul>
  <span class="btn">VIEW PLANS</span>
</section>

<section class="abs plan" style="left:487px">
  <h3>HYBRID SOLUTIONSS</h3>
  <div class="icon"><svg width="24" height="26" viewBox="0 0 14 15"><path d="M7 0 L14 3.5 L7 7 L0 3.5Z" fill="#4aa6ec"/><path d="M0 7 L7 10.5 L14 7M0 10.5 L7 14 L14 10.5" stroke="#555" fill="none" stroke-width="1.6"/></svg></div>
  <p class="price">STARTING AT <b>$19</b>/MO</p>
  <p class="desc">Our Cloud Servers are powered by Hypervia 100% Uptime</p>
  <ul><li>Hypervia Cloud</li><li>Enterprise Ready</li><li>Fully redundant 100% Uptime</li></ul>
  <span class="btn" style="top:203px">VIEW PLANS</span>
</section>

<div class="abs hrule"></div>

<h3 class="abs col-h" style="left:113px">THE NIMBO31 DIFFERENCE</h3>
<div class="abs diff">
  <p>The service we offer is different and our approach is unique. We exceed every industry standard while remaining price competitive. Below are the top differentiators from the rest of the industry.</p>
  <p class="link">Please see The Nimbo31 Difference for a comprehensive list.</p>
</div>
<div class="abs twocol">
  <ul class="list"><li>Network</li><li>Facility</li><li>Support</li><li>Firewall</li></ul>
  <ul class="list"><li>VPN Access</li><li>Servers</li><li>Remote Server Control</li><li>SLA</li></ul>
</div>

<h3 class="abs col-h" style="left:336px">OTHER FACILITIES</h3>
<ul class="abs facilities list">
  <li>Facility</li><li>Power</li><li>Cooling</li><li>Support</li><li>Firewall</li><li>VPN Access</li><li>Remote Server Control</li><li>Service Level Agreements</li>
</ul>

<h3 class="abs col-h" style="left:510px">CUSTOMER SUCCESS STORIES</h3>
<div class="abs arrows"><i></i><i></i></div>
<div class="abs story" style="top:731px">
  <div class="thumb" style="background:#fff;color:#2f86cf">Bytereview</div>
  <p>The largest independent technology review site<span>-Bytereview.com</span></p>
</div>
<div class="abs story" style="top:792px">
  <div class="thumb" style="background:#7fb33a;color:#fff">Larchwell</div>
  <p>Premier Corporate IT Infrastructure Management<span>-Larchwell</span></p>
</div>
<div class="abs story" style="top:853px">
  <div class="thumb" style="background:#17336b;color:#fff">Chirpline</div>
  <p>Leading mobile app providing with over 5 million downloads and 1.5 million monthly unique users<span>-Chirpline</span></p>
</div>

<footer class="abs footer"></footer>
<h3 class="abs foot-h" style="left:98px">ABOUT NIMBO31</h3>
<p class="abs about">Lorem ipsum dolor sit amet, consectetur adipisicing elit, sed do eiusmod tempor incididunt ut labore et dolore magna aliqua. Ut enim ad minim veniam, quis nostrud exercitation ullamco laboris nisi ut aliquip ex ea commodo consequat. Duis aute irure dolor in reprehenderit in voluptate velit esse cillum</p>
<span class="abs more">MORE...</span>

<h3 class="abs foot-h" style="left:341px">QUICK CONTACT</h3>
<div class="abs field" style="top:986px">Name</div>
<div class="abs field" style="top:1015px">Email</div>
<div class="abs field" style="top:1046px;height:40px">Message</div>
<div class="abs submit">SUBMIT</div>

<h3 class="abs foot-h" style="left:551px">FOLLOW US</h3>
<ul class="abs social">
  <li><i></i>friendspace</li>
  <li><i></i>Chirper</li>
  <li><i></i>Workline</li>
  <li><i></i>RSS</li>
</ul>

<div class="abs bottom"></div>
<p class="abs copy">Copyright © 2012. www.nimbo31.com.au</p>

</body>
</html>
```